A clean crisp business card for a Landscape Construction company. Designed to be easy to read contact/ info and also be appealing/interesting, unlike a traditional business card.

Industry/Entity Type

Landscape Construction

Contact Information for Business Card

Company name : Brambleford Landscape Construction, phone number: (877) 62Vista, website:Bramblefordyards.example, Email, sales@bramblefordyards.example

Requirements
Nice to have
• Luxurious finishes/ details…. Icons or emblems next to contact info
Should not have
• Clipart or general pictures

```html
<!DOCTYPE html>
<html lang="en">
<head>
<meta charset="utf-8">
<title>Brambleford Landscape Construction – Business Card</title>
<link rel="stylesheet" href="https://fonts.googleapis.com/css2?family=Cinzel:wght@500&family=Open+Sans:wght@400&display=swap">
<style>
  :root {
    --stage: #c9cbcd;
    --card-dark: #121212;
    --card-light: #ffffff;
    --leaf-green: #9dcb3c;
    --leaf-green-soft: #d6ebaa;
    --river-blue: #2a6ebb;
    --river-blue-soft: #b3cbe8;
    --ink: #222222;
  }
  * { margin: 0; padding: 0; box-sizing: border-box; }
  html, body { width: 1200px; height: 928px; overflow: hidden; }
  body {
    background: var(--stage);
    position: relative;
    font-family: "Open Sans", Arial, sans-serif;
    color: var(--ink);
  }
  .card {
    position: absolute;
    border-radius: 16px;
    overflow: hidden;
  }
  .card-front {
    left: 267px; top: 59px; width: 669px; height: 381px;
    background: var(--card-dark);
  }
  .card-back {
    left: 264px; top: 484px; width: 675px; height: 387px;
    background: var(--card-light);
  }
  .brand {
    font-family: "Cinzel", Georgia, serif;
    font-weight: 500;
    color: var(--leaf-green);
    position: absolute;
  }
  .brand-name { display: block; }
  .brand-tagline { display: block; }
  .card-front .brand {
    left: 0; right: 0; top: 214px; text-align: center;
  }
  .card-front .brand-name { font-size: 44px; line-height: 50px; letter-spacing: 1px; }
  .card-front .brand-tagline { font-size: 16px; letter-spacing: 3.6px; margin-top: 4px; }
  .card-back .brand { left: 38px; top: 108px; }
  .card-back .brand-name { font-size: 32px; line-height: 34px; }
  .card-back .brand-tagline { font-size: 10.5px; letter-spacing: 2.2px; margin-top: 0; }
  .vine-band {
    position: absolute;
    left: 0; top: 168px;
    width: 640px; height: 92px;
    border-radius: 0 46px 46px 0;
    background: linear-gradient(180deg, var(--leaf-green-soft) 0%, var(--leaf-green-soft) 55%, var(--river-blue-soft) 100%);
  }
  .person {
    position: absolute; right: 40px; top: 52px; text-align: right;
  }
  .person-name {
    font-family: "Cinzel", Georgia, serif; font-weight: 500;
    font-size: 26px; letter-spacing: 1.5px; color: var(--river-blue);
  }
  .person-name .surname { color: var(--leaf-green); }
  .person-role { font-size: 15px; letter-spacing: 0.6px; margin-top: 2px; }
  .contact-list {
    position: absolute; left: 38px; top: 270px; list-style: none;
    font-size: 16px;
  }
  .contact-item { display: flex; align-items: center; height: 30px; }
  .contact-item svg { width: 16px; height: 16px; margin-right: 8px; flex: none; }
  .contact-phone { letter-spacing: 1px; }
  .address {
    position: absolute; right: 40px; top: 296px; text-align: right;
    font-size: 15.5px; line-height: 27px; font-style: normal;
  }
</style>
</head>
<body>

<section class="card card-front">
  <div class="brand">
    <span class="brand-name">Brambleford</span>
    <span class="brand-tagline">Landscape Construction</span>
  </div>
</section>

<section class="card card-back">
  <div class="vine-band" role="img" aria-label="Decorative green and blue flowing vine with leaves across the card"></div>

  <div class="brand">
    <span class="brand-name">Brambleford</span>
    <span class="brand-tagline">Landscape Construction</span>
  </div>

  <div class="person">
    <div class="person-name">Elena <span class="surname">Marsh</span></div>
    <div class="person-role">Director</div>
  </div>

  <ul class="contact-list">
    <li class="contact-item contact-phone">
      <svg viewBox="0 0 16 16"><path d="M3.5 1.5 L6 4.5 L4.6 6.2 C5.5 8 7.8 10.4 9.8 11.4 L11.5 10 L14.5 12.5 L12.8 14.6 C7.5 14 2 8.5 1.4 3.2 Z" fill="var(--leaf-green)"/></svg>
      (877) 62Vista
    </li>
    <li class="contact-item">
      <svg viewBox="0 0 16 16"><rect x="1" y="3" width="14" height="10" rx="1" fill="var(--leaf-green)"/><path d="M1.5 3.8 L8 9 L14.5 3.8" stroke="#fff" stroke-width="1.3" fill="none"/></svg>
      sales@bramblefordyards.example
    </li>
    <li class="contact-item">
      <svg viewBox="0 0 16 16"><circle cx="8" cy="8" r="7" fill="var(--leaf-green)"/><path d="M1 8 H15 M8 1 C5 4 5 12 8 15 M8 1 C11 4 11 12 8 15" stroke="#fff" stroke-width="1" fill="none"/></svg>
      www.bramblefordyards.example
    </li>
  </ul>

  <address class="address">
    4120 Harlow Creek Rd<br>
    Suite 12, Fernvale, OH 45000
  </address>
</section>

</body>
</html>
```